My mortgage broker firms requires a DL flyer targeting who need finance to build their home.

The design must be professional in presentation as we a small boutique firm that build relationships with our clients through trust.

Refer to my website marrowfinance.com.au to keep the design in similar taste.

Target Market(s)

People in the market to build their 1st home, investment or upgrade.

Industry/Entity Type

Finance

Colors
ec1f27
ffffff
000000

Requirements
Must have
• Catching to the eye. These flyers will be sitting on the desk at builders display homes with many other brochures.
• Premium feel to the design / branding.
Nice to have
• connect to the emotional feelings of building. Not the transaction. ie building a future for the kids or building their investment portfolio which brings financial freedom etc etc
Should not have
• No money pictures

```html
<!DOCTYPE html>
<html lang="en">
<head>
<meta charset="utf-8">
<title>Marrow Finance – Building a Home DL Flyer</title>
<link rel="stylesheet" href="https://fonts.googleapis.com/css2?family=Carlito:wght@400;700&family=Lato:wght@300;400&display=swap">
<style>
  :root {
    --brand-red: #d7212b;
    --accent-red: #ec1f27;
    --ink: #000000;
    --paper: #ffffff;
    --muted: #5e5e60;
    --footer: #3b3b3d;
    --backdrop: #e6e4e1;
  }
  * { margin: 0; padding: 0; box-sizing: border-box; }
  html, body { width: 911px; height: 1200px; overflow: hidden; background: var(--backdrop); }
  .flyer {
    position: absolute; left: 170px; top: 0;
    width: 571px; height: 1200px;
    background: var(--paper);
    font-family: "Carlito", "Calibri", sans-serif;
    overflow: hidden;
  }
  .hero-photo {
    position: absolute; left: 0; top: 0; width: 571px; height: 453px;
    background: linear-gradient(180deg, #b9c8d6 0%, #d9c3a0 35%, #c9a878 70%, #a98a63 100%);
  }
  .hero-question {
    position: absolute; left: 0; top: 385px; width: 399px; height: 68px;
    background: rgba(255,255,255,0.72);
    color: var(--brand-red); font-weight: 700; font-size: 39px;
    line-height: 68px; padding-left: 25px; letter-spacing: -0.3px;
  }
  .headline-band {
    position: absolute; left: 0; top: 453px; width: 571px; height: 74px;
    background: var(--brand-red); color: var(--paper);
    font-weight: 700; font-size: 36px; line-height: 70px; padding-left: 23px;
  }
  .brand {
    position: absolute; left: 76px; top: 565px; height: 87px;
    display: flex; align-items: center; gap: 20px;
  }
  .brand-dot { width: 87px; height: 87px; border-radius: 50%; background: var(--accent-red); }
  .brand-name { font-size: 46px; font-weight: 700; color: var(--ink); }
  .copy {
    position: absolute; left: 30px; width: 516px;
    text-align: justify; font-size: 19.5px; line-height: 27px;
  }
  .copy-lead { top: 676px; color: var(--ink); text-align: left; }
  .copy-body { font-family: "Lato", sans-serif; font-weight: 300; font-size: 19px; color: var(--muted); }
  .copy-1 { top: 786px; }
  .copy-2 { top: 866px; }
  .copy-3 { top: 973px; }
  .cta { color: var(--brand-red); font-weight: 400; }
  .footer-rule { position: absolute; left: 0; top: 1060px; width: 571px; height: 13px; background: var(--accent-red); }
  .footer {
    position: absolute; left: 0; top: 1073px; width: 571px; height: 127px;
    background: var(--footer); color: var(--paper);
    padding: 17px 0 0 47px; font-size: 21px;
  }
  .contact { display: flex; align-items: center; gap: 13px; height: 30px; }
  .contact svg { width: 20px; height: 20px; flex: none; }
</style>
</head>
<body>
<div class="flyer">
  <div class="hero-photo" role="img" aria-label="Photo of a smiling family standing inside the timber frame of their new home under construction"></div>
  <div class="hero-question">BUILDING A HOME?</div>
  <div class="headline-band">GET THE FOUNDATIONS RIGHT.</div>

  <div class="brand">
    <div class="brand-dot"></div>
    <div class="brand-name">Marrow Finance</div>
  </div>

  <p class="copy copy-lead">Sometimes the hardest part about building your home is organising the finance. And if you’ve ever done it before, you’ll know it can be trickier than your average mortgage.</p>
  <p class="copy copy-body copy-1">Whether it is your first build, an investment property or even an upgrade—its worth getting in touch.</p>
  <p class="copy copy-body copy-2">I will help you find a great home loan, while talking you through ways to reduce your costs and maximise the value of the build.</p>
  <p class="copy copy-body copy-3"><span class="cta">GET YOUR FINANCIAL FOUNDATIONS RIGHT</span>—it could make all the difference to the affordability of your project.</p>

  <div class="footer-rule"></div>
  <div class="footer">
    <div class="contact">
      <svg viewBox="0 0 20 20"><circle cx="10" cy="10" r="10" fill="#ec1f27"/><path d="M6.5 5.5l2 0 .8 2.3-1.2 1a6 6 0 0 0 3.1 3.1l1-1.2 2.3.8 0 2c-4.5.3-8.3-3.5-8-8z" fill="#fff"/></svg>
      <span>02 4000 1234</span>
    </div>
    <div class="contact">
      <svg viewBox="0 0 20 20"><circle cx="10" cy="10" r="10" fill="#ec1f27"/><g fill="none" stroke="#fff" stroke-width="1.2"><circle cx="10" cy="10" r="5.5"/><ellipse cx="10" cy="10" rx="2.4" ry="5.5"/><path d="M4.5 10h11M5.3 7.2h9.4M5.3 12.8h9.4"/></g></svg>
      <span>www.marrowfinance.com.au</span>
    </div>
    <div class="contact">
      <svg viewBox="0 0 20 20"><circle cx="10" cy="10" r="10" fill="#ec1f27"/><path d="M10 4a3.6 3.6 0 0 0-3.6 3.6c0 2.7 3.6 7.4 3.6 7.4s3.6-4.7 3.6-7.4A3.6 3.6 0 0 0 10 4z" fill="#fff"/><circle cx="10" cy="7.6" r="1.3" fill="#ec1f27"/></svg>
      <span>18 Harbour Lane, Kellview NSW 2399</span>
    </div>
  </div>
</div>
</body>
</html>
```